Moravel Aesthetic Doctor

I require an elegant, luxurious looking business card for my aesthetic business. I am a doctor and that will set me aside from competitors. I am planning to provide home and spa based treatments to clients with high expectations. I have attached my logo.

```html
<!DOCTYPE html>
<html lang="en">
<head>
<meta charset="utf-8">
<title>Moravel Aesthetic Doctor – Business Card</title>
<link href="https://fonts.googleapis.com/css2?family=Marcellus&family=Roboto:wght@300;400;500;700&display=swap" rel="stylesheet">
<style>
  :root {
    --stage: #5b5d60;
    --blue-light: #27b0e6;
    --blue-deep: #1b68c2;
    --sky: #5cbde9;
    --grey-band: #a8aaac;
    --grey-text: #8c8e91;
    --white: #ffffff;
  }
  * { box-sizing: border-box; margin: 0; padding: 0; }
  html, body { width: 1200px; height: 1124px; overflow: hidden; background: var(--stage); }
  .canvas { position: relative; width: 1200px; height: 1124px; }

  .card {
    position: absolute; left: 150px; width: 900px; height: 514px;
    overflow: hidden; box-shadow: 0 6px 18px rgba(0,0,0,.35);
  }

  /* Back */
  .card-back {
    top: 28px;
    background: linear-gradient(160deg, var(--blue-light) 0%, #2490d8 45%, var(--blue-deep) 100%);
    color: var(--white);
  }
  .card-back .brand { position: absolute; left: 0; right: 0; top: 120px; display: flex; justify-content: center; align-items: center; gap: 24px; }
  .brand-dot { width: 86px; height: 86px; border-radius: 50%; border: 3px solid rgba(255,255,255,.85); flex: none; }
  .brand-name { font-family: "Marcellus", serif; font-weight: 400; line-height: 1; }
  .brand-name .main { display: block; font-size: 74px; letter-spacing: 4px; }
  .brand-name .sub { display: block; font-size: 27px; letter-spacing: 3.5px; margin-top: 6px; }
  .card-back .brand-name { color: var(--white); }
  .services { position: absolute; left: 0; right: 0; top: 318px; text-align: center; font-family: "Roboto", sans-serif; font-weight: 400; font-size: 22px; line-height: 1.45; }
  .services .sep { margin: 0 6px; }

  /* Front */
  .card-front { top: 582px; background: var(--white); }
  .card-front .brand { position: absolute; left: 0; right: 0; top: 52px; display: flex; justify-content: center; align-items: center; gap: 22px; }
  .card-front .brand-dot { border-color: var(--sky); }
  .card-front .brand-name { color: var(--grey-text); }
  .holder-band { position: absolute; left: 0; right: 0; top: 202px; height: 122px; background: var(--grey-band); color: var(--white); text-align: center; font-family: "Roboto", sans-serif; padding-top: 20px; }
  .holder-name { font-size: 31px; font-weight: 700; }
  .holder-name .post { font-size: 19px; font-weight: 500; margin-left: 4px; }
  .holder-title { font-size: 23px; font-weight: 300; margin-top: 6px; letter-spacing: .3px; }

  .social { position: absolute; top: 350px; left: 0; right: 0; display: flex; justify-content: center; gap: 22px; }
  .social span { width: 30px; height: 30px; border-radius: 50%; background: var(--sky); }

  .contacts { position: absolute; top: 402px; left: 0; right: 0; display: flex; justify-content: center; gap: 38px; font-family: "Roboto", sans-serif; font-weight: 300; font-size: 24px; color: var(--grey-text); }
  .contact { display: flex; align-items: center; gap: 12px; }
  .contact svg { width: 22px; height: 22px; fill: none; stroke: var(--sky); stroke-width: 2; }
  .contact .accent { color: var(--sky); }
</style>
</head>
<body>
<div class="canvas">

  <section class="card card-back" aria-label="Card back">
    <div class="brand">
      <span class="brand-dot"></span>
      <div class="brand-name"><span class="main">MORAVEL</span><span class="sub">AESTHETIC DOCTOR</span></div>
    </div>
    <p class="services">
      Dermal injectables<span class="sep">•</span>Plasma facials<span class="sep">•</span>Microneedling<br>
      Skin boosters<span class="sep">•</span>Excessive sweating<br>
      Home and Spa Based Treatments
    </p>
  </section>

  <section class="card card-front" aria-label="Card front">
    <div class="brand">
      <span class="brand-dot"></span>
      <div class="brand-name"><span class="main">MORAVEL</span><span class="sub">AESTHETIC DOCTOR</span></div>
    </div>

    <div class="holder-band">
      <p class="holder-name">Dr Elise Varnholt,<span class="post">MRCPCH MD</span></p>
      <p class="holder-title">Australasian Diploma of Aesthetic Medicine</p>
    </div>

    <div class="social" aria-label="Social profiles"><span></span><span></span></div>

    <div class="contacts">
      <p class="contact">
        <svg viewBox="0 0 24 24"><path d="M5 3h4l2 5-3 2a12 12 0 0 0 6 6l2-3 5 2v4a2 2 0 0 1-2 2A17 17 0 0 1 3 5a2 2 0 0 1 2-2z" fill="#5cbde9" stroke="none"/></svg>
        0800 555 014
      </p>
      <p class="contact">
        <svg viewBox="0 0 24 24"><rect x="3" y="6" width="18" height="12" rx="1"/><path d="M3 7l9 6 9-6"/></svg>
        elise@moravel.co.nz
      </p>
      <p class="contact">
        <svg viewBox="0 0 24 24"><circle cx="12" cy="12" r="9"/><ellipse cx="12" cy="12" rx="4" ry="9"/><path d="M3 12h18M5 7h14M5 17h14"/></svg>
        www.<span class="accent">moravel</span>.co.nz
      </p>
    </div>
  </section>

</div>
</body>
</html>
```